Business card design for holistic health care clinic

We need a double-sided business card design for our holistic health care clinic that integrates our logo design and also its color scheme. My business is called Valmira. It is an integrative medicine clinic. You have already done the logo for me. Please ensure an elegant and upscale design that is not cluttered, but still has all the necessary information (please see below for details).

Target Market(s)

Wellness, fitness, rehabilitation for educated, well-traveled open-minded clients who are focused on natural, organic, balanced and preventive healthcare and lifestyle.

Industry/Entity Type

Medical

Contact Information for Business Card

Modern, clean.

Number of Pages Required

1 page

Font styles to use
Serif
Sans Serif

Colors

Designer to choose colors to be used in the design.

Requirements
Must have
• Logo on one side, all other information on the other side.
• Other information should include:
• Tobias Wrenfeld - DOE, CPT, LMT
• 4100 East Marrow Drive
• Austin, TX 78119
• 512 555 0148
• 818 555 0192
• info@ValmiraHealth.example
• t.wrenfeld@ValmiraHealth.example
Nice to have
• Darker background on front - but not totally black - shaded/dark gray.

```html
<!DOCTYPE html>
<html lang="en">
<head>
<meta charset="utf-8">
<title>Valmira – Business Card</title>
<link href="https://fonts.googleapis.com/css2?family=Roboto:ital,wght@0,400;0,700;1,400&family=Roboto+Condensed:wght@400;700&display=swap" rel="stylesheet">
<style>
  :root {
    --stage: #e9e7e3;
    --card-dark: #2f3032;
    --card-light: #f7f7f7;
    --brand-blue: #1a93d6;
    --text-light: #e6e6e6;
    --text-muted: #5a5a5a;
    --rule-light: #8a8a8a;
  }
  html, body {
    margin: 0;
    padding: 0;
    width: 1200px;
    height: 911px;
    overflow: hidden;
    background: var(--stage);
  }
  .canvas {
    position: relative;
    width: 1200px;
    height: 911px;
  }
  .card {
    position: absolute;
    width: 540px;
    height: 310px;
    border-radius: 20px;
    box-shadow: 0 10px 24px rgba(0,0,0,0.18);
    overflow: hidden;
  }
  /* Front: contact details */
  .card-front {
    left: 60px;
    top: 140px;
    background: var(--card-dark);
    color: var(--text-light);
    font-family: "Roboto", sans-serif;
  }
  .contact-block {
    position: absolute;
    left: 44px;
    top: 40px;
    width: 300px;
  }
  .holder-name {
    font-family: "Roboto Condensed", sans-serif;
    font-weight: 700;
    font-size: 21px;
    letter-spacing: 0.5px;
    color: var(--brand-blue);
    text-transform: uppercase;
    margin: 0;
  }
  .holder-credentials {
    font-family: "Roboto Condensed", sans-serif;
    font-weight: 400;
    font-size: 12px;
    color: var(--brand-blue);
    letter-spacing: 0.3px;
  }
  .divider {
    border: 0;
    border-top: 1px dashed var(--rule-light);
    width: 200px;
    margin: 16px 0;
  }
  .address {
    font-size: 14px;
    line-height: 1.45;
    margin: 0;
  }
  .contact-list {
    list-style: none;
    margin: 0;
    padding: 0;
    font-size: 14px;
    line-height: 1.6;
  }
  .contact-list li {
    display: flex;
    align-items: center;
    gap: 9px;
  }
  .contact-icon {
    width: 12px;
    height: 12px;
    flex: none;
    fill: var(--brand-blue);
  }
  /* Back: brand */
  .card-back {
    left: 600px;
    top: 460px;
    background: var(--card-light);
    font-family: "Roboto", sans-serif;
  }
  .brand-lockup {
    position: absolute;
    left: 0;
    right: 0;
    top: 100px;
    text-align: center;
  }
  .brand-name {
    display: inline-flex;
    align-items: center;
    gap: 14px;
    font-weight: 700;
    font-size: 58px;
    letter-spacing: 2px;
    color: var(--brand-blue);
    text-transform: uppercase;
    margin: 0;
  }
  .brand-dot {
    width: 14px;
    height: 14px;
    border-radius: 50%;
    background: var(--brand-blue);
  }
  .tagline-row {
    display: flex;
    align-items: center;
    justify-content: center;
    gap: 14px;
    margin-top: 22px;
  }
  .tagline-rule {
    width: 70px;
    height: 1px;
    background: var(--brand-blue);
  }
  .tagline {
    font-style: italic;
    font-size: 15px;
    color: var(--text-muted);
    margin: 0;
  }
</style>
</head>
<body>
<main class="canvas">

  <section class="card card-front" aria-label="Business card front">
    <div class="contact-block">
      <p class="holder-name">Tobias Wrenfeld <span class="holder-credentials">- DOE, CPT, LMT</span></p>
      <hr class="divider">
      <p class="address">4100 East Marrow Drive<br>Austin, TX 78119</p>
      <hr class="divider">
      <ul class="contact-list">
        <li>
          <svg class="contact-icon" viewBox="0 0 12 12" aria-hidden="true"><path d="M2.4 0.8 L4.4 2.8 L3.3 4.2 C4 5.8 6.2 8 7.8 8.7 L9.2 7.6 L11.2 9.6 L9.8 11.2 C5.4 11 1 6.6 0.8 2.2 Z"/></svg>
          <span>512 555 0148</span>
        </li>
        <li>
          <svg class="contact-icon" viewBox="0 0 12 12" aria-hidden="true"><path d="M1 1 H11 V11 H1 Z M2.4 2.4 V9.6 H9.6 V2.4 Z"/></svg>
          <span>818 555 0192</span>
        </li>
        <li>
          <svg class="contact-icon" viewBox="0 0 12 12" aria-hidden="true"><path d="M0.5 2 H11.5 V10 H0.5 Z"/><path d="M0.8 2.3 L6 6.5 L11.2 2.3" stroke="#2f3032" stroke-width="1.1" fill="none"/></svg>
          <span>t.wrenfeld@ValmiraHealth.example</span>
        </li>
        <li>
          <svg class="contact-icon" viewBox="0 0 12 12" aria-hidden="true"><circle cx="6" cy="6" r="5.5"/><path d="M0.8 6 H11.2 M6 0.6 C3.5 3.5 3.5 8.5 6 11.4 M6 0.6 C8.5 3.5 8.5 8.5 6 11.4" stroke="#2f3032" stroke-width="0.9" fill="none"/></svg>
          <span>www.ValmiraHealth.example</span>
        </li>
      </ul>
    </div>
  </section>

  <section class="card card-back" aria-label="Business card back">
    <div class="brand-lockup">
      <p class="brand-name"><span class="brand-dot" aria-hidden="true"></span>Valmira</p>
      <div class="tagline-row">
        <span class="tagline-rule" aria-hidden="true"></span>
        <p class="tagline">helping the body help itself</p>
        <span class="tagline-rule" aria-hidden="true"></span>
      </div>
    </div>
  </section>

</main>
</body>
</html>
```